Yoga/movement guide/teacher for adult yoga practice and kid yoga

What is the positioning or mission statement of your company? to guide individuals in a yoga-based safe and sustainable movement practice applicable to all ages and body types. Currently my focus is working with children in daycare and school settings, but my goal is to expand into private yoga practice for adults, and potentially as part of rented space in studios. I hope to find a way to work with children AND adults (so would love for logo to be appealing to both), but current focus is with children based on need and demand in the community. yoga for children also compliments my backround as a pediatrician/neonatologist, and I greatly miss interacting with children. I also want to emphasize a yoga/movement practice that is focused more on what one feels internally through movement. NOT what one looks like asthetically. I believe in removing all mirrors from yoga/movement practice. It should be an experience of movement/poses/yoga through appropriate cueing and education. It is not about the details of how far the knee should bend, or how high the leg should be. Focusing on foudation first, core, then core engagement and ultimately expression of poses/movements. A focus on strength, stability and mobility, not just flexibility, which is the common perception/association with yoga. I also want individuals to learn to be an advocate of their own health. Through guidance, I hope for individuals to connect with their body so they know themselves so well to be able to advocate for themselves in the modern healthcare world. This internal experience and connection is so essential in a world where modern medicine has become a business and it is all about making a dollar. the connection with patients is lost, and individuals need to learn to empower themselves and through their new found voice to be able to articulate what is wrong.<br/>Does your company have a tagline or slogan that should be included with the logo? "Move With Inner Light"<br/>What do you hope your company can be known for? Accessible yoga for a sustained practice. A guided movement practice where one gains information and knowledge of oneself through a mind/body connection. For one feel good physically with a new awaraness of their internal radiance that exists in all beings. Physical rejuvenation egnites a light and increases energy to flow through the physical body, which ultimately tranlates into works of kindness for others and out in the world. <br/>What color palettes might you prefer? why? love the colors currently chosen<br/>Where will the logo be primarily used? initially business cards, but hopefully future websites, t-shirts, and potentially local magazine adds. Also starting with a small couple of banners for community events in the area. I currently practice as a nomad out of my car :)<br/>Are there any elements you would prefer to see in the logo? Movement. A modern depiction of a human body/figure practicing movement. Hoping to avoid a stereotypical yoga pose per say, just because I want to people to think of it more of a movement practice with yoga roots. Modern yoga. There are elements of breathing and connecting with oneself through the flow of breath and movement, but I do not focus on the meditative/cerebral aspect of the yoga practice. What I teach is almost reaching a meditative state through movement. I personally don't practice, nor resonate with just seated meditation. just not my thing :)<br/>In your opinion, what defines a well-designed logo? curiosity. enough info for individuals to think they know what it means, but want to know more. invokes curiosity, but not too abstract. Reproducible. not too complicated. I want also to invoke a community feel, so a design that appeals to all people within a community. <br/>What is your preference in reference to icons, typography, spokespeople (characters), etc.? modern design. I love the idea of a logo for my purposes, to invoke a sense of movement from within. So not too static. <br/>What words or icons must be included in the logo? movement with yoga roots. <br/>What logos do you like and why? A representation, but not exact. I think some ambiguity is intriguing for others, and also memorable. I want it to be an artistic representation of movement/yoga<br/>What logos do you dislike and why? too busy, too loud. <br/>In your opinion, what is the primary purpose for a logo? association<br/>Who is the primary target audience? (who is most likely to use your services/product?) Children and their parents, but ultimately to expand into teaching adults. I even have aspirations of prenatal and post-natal yoga. Potentially incorporating infants. <br/>Who currently uses your product the most? n/a (working in schools/daycare currently. It is currently all volunteer)<br/>Are you pleased with the range of people your company serves? n/a<br/>Are you looking to expand, modify, or completely change your target audience? or will it remain the same? yes! expand into an adult audience. <br/>How do you plan to focus on your target audience? currently by working through schools and daycares. hopefully ultimately through after school care programs and then offering kid yoga in an existing yoga studio (working on this with Q Studio in Ridgeland, currently)<br/>What are your main forms of advertising? word of mouth, schools, daycares. Happy kids talking to their parents about the yoga class they took and happy teachers :)<br/>How do most customers find out about your company?<br/>Which gender are you targeting? All genders! However, with kid yoga, often the maternal individual in the child's life is more involved with decision making as far as extracurricular activities

Target Market(s)

individuals and families interested in wellness and feeling great

Contact Information for Business Card

Dana Whitford
Yoga Instructor
RYT-200, RCYT

certified yoga teacher for adults and children

Colors

Designer to choose colors to be used in the design.

Requirements
Must have
• "Move With Inner Light"
Nice to have
• logo with same colors

```html
<!DOCTYPE html>
<html lang="en">
<head>
<meta charset="utf-8">
<title>Brightwell Studios – Business Card</title>
<link href="https://fonts.googleapis.com/css2?family=Lato:wght@300;400;900&display=swap" rel="stylesheet">
<style>
  :root {
    --backdrop: #7a7a7a;
    --card-yellow: #e8ca18;
    --card-yellow-light: #f6dd45;
    --card-dark: #262626;
    --ink: #151515;
    --brand-grey: #a3a3a3;
    --brand-yellow: #f3d83a;
    --brand-teal: #5fc8cf;
  }
  * { margin: 0; padding: 0; box-sizing: border-box; }
  html, body { width: 1200px; height: 1200px; overflow: hidden; }
  body {
    position: relative;
    background: var(--backdrop);
    font-family: "Lato", sans-serif;
  }
  .card {
    position: absolute;
    top: 303px;
    width: 369px;
    height: 594px;
    overflow: hidden;
  }
  .card--front {
    left: 229px;
    background: linear-gradient(160deg, var(--card-yellow) 0%, var(--card-yellow) 45%, var(--card-yellow-light) 100%);
    color: var(--ink);
    text-align: center;
  }
  .card--back {
    left: 630px;
    background: var(--card-dark);
  }
  .holder-name {
    position: absolute;
    top: 140px;
    left: 0; right: 0;
    font-weight: 900;
    font-size: 22px;
    letter-spacing: 0.2px;
  }
  .holder-role {
    position: absolute;
    top: 163px;
    left: 0; right: 0;
    font-size: 17px;
  }
  .contact-icons {
    position: absolute;
    top: 193px;
    left: 89px;
    width: 191px;
    height: 26px;
  }
  .contact-list, .address {
    position: absolute;
    left: 0; right: 0;
    font-size: 17px;
    line-height: 22px;
  }
  .contact-list { top: 229px; }
  .divider {
    position: absolute;
    top: 304px;
    left: 89px;
    width: 196px;
    height: 1px;
    background: rgba(21,21,21,0.45);
  }
  .address { top: 316px; }
  .brand {
    position: absolute;
    top: 305px;
    left: 0; right: 0;
    display: flex;
    align-items: center;
    justify-content: center;
    gap: 12px;
  }
  .brand-dot {
    width: 30px; height: 30px;
    border-radius: 50%;
    background: var(--brand-yellow);
  }
  .brand-name {
    font-weight: 300;
    font-size: 32px;
    color: var(--brand-grey);
  }
  .tagline {
    position: absolute;
    top: 397px;
    left: 175px;
    font-size: 11px;
    letter-spacing: 1.6px;
    text-transform: uppercase;
    color: var(--brand-teal);
    white-space: nowrap;
  }
</style>
</head>
<body>
  <section class="card card--front">
    <h1 class="holder-name">MARCUS ELLERY</h1>
    <p class="holder-role">Managing Director</p>
    <svg class="contact-icons" viewBox="0 0 191 26" aria-hidden="true">
      <line x1="0" y1="13" x2="52" y2="13" stroke="#151515" stroke-width="1"/>
      <line x1="139" y1="13" x2="191" y2="13" stroke="#151515" stroke-width="1"/>
      <circle cx="69" cy="13" r="12" fill="#151515"/>
      <path d="M62 16 h14 v3 h-14z M64 10 h10 l2 5 h-14z" fill="var(--card-yellow)"/>
      <circle cx="95" cy="13" r="12" fill="#151515"/>
      <rect x="87" y="8" width="16" height="11" fill="none" stroke="var(--card-yellow)" stroke-width="1.5"/>
      <path d="M87 8 l8 6 l8 -6" fill="none" stroke="var(--card-yellow)" stroke-width="1.5"/>
      <circle cx="121" cy="13" r="12" fill="#151515"/>
      <circle cx="121" cy="13" r="7" fill="none" stroke="var(--card-yellow)" stroke-width="1.5"/>
      <path d="M114 13 h14 M121 6 c-4 4 -4 10 0 14 M121 6 c4 4 4 10 0 14" fill="none" stroke="var(--card-yellow)" stroke-width="1.2"/>
    </svg>
    <p class="contact-list">044-310 582 764<br>hello@brightwell.com<br>www.brightwellyoga.com</p>
    <div class="divider"></div>
    <p class="address">318, Linden Row Lane,<br>47120,Marlow County</p>
  </section>

  <section class="card card--back">
    <div class="brand">
      <span class="brand-dot"></span>
      <span class="brand-name">Brightwell Studios</span>
    </div>
    <p class="tagline">Move With Inner Light</p>
  </section>
</body>
</html>
```